MRT Property - Business Cards

Looking for a business card & general letterhead, signage etc design for our new logo.

Colours:
000a20
0056a2
00b5ef
0088ce
68cef2

Fonts:
Poppins
Karla

Please keep look and feel of new brand - example in the zip package I sent.

```html
<!DOCTYPE html>
<html lang="en">
<head>
<meta charset="utf-8">
<title>MRT Property – Business Cards</title>
<link rel="stylesheet" href="https://fonts.googleapis.com/css2?family=Poppins:wght@400;700;800&display=swap">
<style>
  :root {
    --ink: #000a20;
    --card-dark: #0c1120;
    --navy: #0056a2;
    --sky: #00b5ef;
    --azure: #0088ce;
    --ice: #68cef2;
    --front-mark: #0a74b4;
    --paper: #c8c8c8;
    --white: #ffffff;
  }
  * { box-sizing: border-box; margin: 0; padding: 0; }
  html, body {
    width: 1200px; height: 900px; overflow: hidden;
    background: var(--paper);
    font-family: "Poppins", sans-serif;
  }
  .sheet {
    position: relative; width: 1200px; height: 900px;
    display: flex; flex-direction: column; align-items: center; justify-content: center; gap: 60px;
  }
  .card {
    width: 600px; height: 343px; border-radius: 38px;
    position: relative; overflow: hidden;
  }
  .card--front {
    background: var(--azure);
    display: flex; align-items: center; justify-content: center;
  }
  .front-brand {
    font-weight: 800; font-size: 62px; letter-spacing: 1px;
    color: var(--front-mark); display: flex; align-items: center; gap: 22px;
  }
  .front-brand .dot {
    width: 46px; height: 46px; border-radius: 50%; background: var(--front-mark);
  }
  .card--back {
    background: var(--card-dark);
    display: grid; grid-template-columns: 268px 2px 1fr; align-items: center;
  }
  .contact {
    text-align: right; padding-right: 22px; color: var(--white);
    font-size: 14px; line-height: 1.35;
  }
  .contact__name {
    font-weight: 800; font-size: 23px; color: var(--navy);
    text-transform: uppercase; letter-spacing: 0.5px; line-height: 1.1;
  }
  .contact__role { font-size: 15px; margin-bottom: 12px; }
  .contact__address { margin-bottom: 12px; }
  .contact__line { display: flex; justify-content: flex-end; align-items: center; gap: 8px; }
  .contact__line svg { width: 13px; height: 13px; flex: none; }
  .divider { width: 2px; height: 230px; background: var(--ice); }
  .back-brand {
    justify-self: center; font-weight: 800; font-size: 40px;
    color: var(--navy); display: flex; align-items: center; gap: 14px;
  }
  .back-brand .dot { width: 30px; height: 30px; border-radius: 50%; background: var(--navy); }
</style>
</head>
<body>
<main class="sheet">
  <section class="card card--front" aria-label="Business card front">
    <div class="front-brand"><span class="dot"></span>MRT Property</div>
  </section>

  <section class="card card--back" aria-label="Business card back">
    <div class="contact">
      <p class="contact__name">Daniel Reeve</p>
      <p class="contact__role">Managing Director</p>
      <p class="contact__address">Your address, City<br>State, Zip 1234</p>
      <p class="contact__line">123 456 789
        <svg viewBox="0 0 16 16"><path fill="var(--sky)" d="M4 1l3 3-2 2c1 2 3 4 5 5l2-2 3 3-2 2C7 14 2 9 2 3z"/></svg>
      </p>
      <p class="contact__line">info@yourmail.com
        <svg viewBox="0 0 16 16"><rect x="1" y="3" width="14" height="10" rx="1" fill="var(--sky)"/><path d="M1 4l7 5 7-5" stroke="var(--card-dark)" stroke-width="1.4" fill="none"/></svg>
      </p>
      <p class="contact__line">www.yourwebsite.com
        <svg viewBox="0 0 16 16"><circle cx="8" cy="8" r="7" fill="var(--sky)"/><path d="M1 8h14M8 1c3 3 3 11 0 14M8 1c-3 3-3 11 0 14" stroke="var(--card-dark)" stroke-width="1.1" fill="none"/></svg>
      </p>
    </div>
    <div class="divider"></div>
    <div class="back-brand"><span class="dot"></span>MRT Property</div>
  </section>
</main>
</body>
</html>
```